New business stationairy

I need paper with header and footer and business cards.
I am a Ltd Company and my main field of expertise is QA/QC inspection in the Oil and Gas Industry. I will need all contact detail inserted and a footer with registration number and bank details etc

```html
<!DOCTYPE html>
<html lang="en">
<head>
<meta charset="utf-8">
<title>Halden Inspection Services Ltd – Letterhead</title>
<link rel="stylesheet" href="https://fonts.googleapis.com/css2?family=Open+Sans:wght@700&family=Cabin:wght@400;500&display=swap">
<style>
  :root {
    --backdrop: #ececec;
    --paper: #ffffff;
    --brand-blue: #2450e0;
    --text-blue: #2342d6;
    --art-blue: #3d7ee6;
    --rule-blue: #8fa6ee;
  }
  * { margin: 0; padding: 0; box-sizing: border-box; }
  html, body {
    width: 912px;
    height: 1200px;
    overflow: hidden;
    background: var(--backdrop);
  }
  .letterhead {
    position: absolute;
    left: 34px;
    top: 76px;
    width: 850px;
    height: 1070px;
    background: var(--paper);
  }
  .header-art {
    position: absolute;
    display: block;
  }
  .header-art--pumpjack { left: 26px; top: 24px; width: 125px; height: 135px; }
  .header-art--refinery { left: 661px; top: 52px; width: 157px; height: 92px; }

  .company {
    position: absolute;
    left: 0;
    width: 850px;
    top: 18px;
    padding-left: 16px;
    text-align: center;
    color: var(--text-blue);
  }
  .company-name {
    font-family: "Open Sans", Arial, sans-serif;
    font-weight: 700;
    font-size: 29px;
    letter-spacing: -0.2px;
    color: var(--brand-blue);
    line-height: 40px;
  }
  .company-address {
    margin-top: 10px;
    font-family: "Cabin", "Gill Sans", sans-serif;
    font-size: 17px;
    line-height: 23px;
  }
  .company-reg {
    margin-top: 3px;
    font-family: "Cabin", "Gill Sans", sans-serif;
    font-size: 11px;
  }

  .rule {
    position: absolute;
    height: 1.5px;
    background: var(--rule-blue);
  }
  .rule--header { left: 53px; top: 156px; width: 763px; }
  .rule--footer { left: 46px; top: 999px; width: 772px; }

  .footer-contact {
    position: absolute;
    left: 46px;
    width: 772px;
    top: 1010px;
    padding-left: 36px;
    text-align: center;
    font-family: "Cabin", "Gill Sans", sans-serif;
    font-size: 16px;
    color: var(--text-blue);
  }
  .footer-contact .separator { margin: 0 18px; }
</style>
</head>
<body>
  <main class="letterhead">
    <svg class="header-art header-art--pumpjack" viewBox="0 0 125 135" role="img" aria-label="Silhouette illustration of an oil pump jack">
      <rect width="125" height="135" fill="var(--art-blue)" opacity="0.85"/>
    </svg>

    <header class="company">
      <h1 class="company-name">Halden Inspection Services Ltd</h1>
      <p class="company-address">The Willows, Mill Lane, Ashcombe, Hartley Bridge,<br>Dorset DT9 4QL</p>
      <p class="company-reg">Reg. #4827316</p>
    </header>

    <svg class="header-art header-art--refinery" viewBox="0 0 157 92" role="img" aria-label="Silhouette illustration of a refinery with smoking chimneys">
      <rect width="157" height="92" fill="var(--art-blue)" opacity="0.85"/>
    </svg>

    <div class="rule rule--header"></div>

    <div class="rule rule--footer"></div>
    <footer class="footer-contact">
      <span class="contact-email">email: office2207@mailbox.co.uk</span><span class="separator">•</span><span class="contact-mobile">mobile: 07700 900418</span>
    </footer>
  </main>
</body>
</html>
```